Business card design for modern PanoWalk agency

Hello,

I need a business card design for my company Kites7Market.
We mainly offer Zorvex PanoWalk Tours (360° Photography) and it should be a business card with following details:

Name: Tobias Wendler
Number: +49 176 58 20 917
Mail: tobias@kites7market.com
website: kites7market.com

Main colour that we use is the red of the logo.
It´s also important to integrate the "Zorvex Verified logo" as the person on this business card is a Zorvex verified photographer.

And if possible we would also like to integrate something like send us a sms or chatterly and we call you back. As the number is german but we sell now in Vienna, Austria.

We offer a good price but very high photography quality, as we are mostly students - that´s our concept.

Maybe an idea is to integrate something 360° on the back-side of the card, for example the photo attached (just an idea) or some great design.
See flyer (attached) and kites7market.com for inspiration, maybe use of the photo of me (attached) in a circle or something

I´m very excited for your designs and thanks a lot in advance!! :)

Target Market(s)

Shops, hotels, shopping centers, etc. in Vienna, Austria

Industry/Entity Type

Business

Contact Information for Business Card

double-sided, use red of the logo, 360° zorvex pano walk certified photographer

Font styles to use
Serif
Sans Serif

Colors
ec1f27

Requirements
Nice to have
• maybe some 360° design on back-side
• maybe include photo of me in a circle or something or sketched in red colour

```html
<!DOCTYPE html>
<html lang="en">
<head>
<meta charset="utf-8">
<title>Kites7Market – Business Card</title>
<link rel="stylesheet" href="https://fonts.googleapis.com/css2?family=Oswald:wght@400;500&family=Roboto+Condensed:wght@400&family=Source+Sans+3:ital,wght@0,400;1,400&display=swap">
<style>
  :root {
    --brand-red: #e21a37;
    --brand-grey: #a3a4a8;
    --band-grey: #b5b6ba;
    --paper: #ffffff;
    --stage: #2b2b2b;
    --ink-light: #ffffff;
    --verified-green: #2e9e4f;
  }
  * { margin: 0; padding: 0; box-sizing: border-box; }
  html, body { width: 1200px; height: 987px; overflow: hidden; }
  body { background: var(--stage); position: relative; }

  .card {
    position: absolute;
    left: 293px;
    width: 615px;
    height: 352px;
    overflow: hidden;
  }
  .card--front { top: 130px; background: var(--paper); }
  .card--back { top: 505px; background: var(--brand-red); }

  /* front */
  .front-shape { position: absolute; inset: 0; }
  .brand { position: absolute; display: flex; align-items: center; gap: 10px; }
  .brand--front { left: 33px; top: 76px; }
  .brand-square { width: 100px; height: 75px; background: var(--brand-red); }
  .brand-name {
    font-family: "Oswald", sans-serif;
    font-weight: 500;
    font-size: 38px;
    line-height: 36px;
    color: var(--brand-grey);
    text-transform: uppercase;
  }
  .portrait {
    position: absolute;
    left: 408px; top: 29px;
    width: 160px; height: 160px;
    border-radius: 50%;
    background: radial-gradient(circle at 50% 40%, #8a8d90 0%, #55595c 55%, #3a3d40 100%);
  }
  .holder-name {
    position: absolute;
    right: 331px; top: 282px;
    font-family: "Oswald", sans-serif;
    font-weight: 500;
    font-size: 31px;
    line-height: 1;
    color: var(--ink-light);
    text-transform: uppercase;
    white-space: nowrap;
  }
  .contact-divider {
    position: absolute;
    left: 306px; top: 264px;
    width: 1.5px; height: 65px;
    background: var(--ink-light);
  }
  .contact-list { position: absolute; left: 330px; top: 262px; list-style: none; }
  .contact-item {
    display: flex; align-items: center; gap: 6px;
    height: 23px;
    font-family: "Roboto Condensed", sans-serif;
    font-size: 16px;
    color: var(--ink-light);
  }
  .contact-icon { width: 13px; height: 13px; fill: var(--ink-light); flex: none; }

  /* back */
  .venue-photo {
    position: absolute; left: 0; top: 0;
    width: 615px; height: 284px;
    background: linear-gradient(100deg, #6a3a2a 0%, #8c2a2a 25%, #d8c3a0 45%, #cdb590 65%, #b38a5a 85%, #9a6a45 100%);
  }
  .verified-badge { position: absolute; left: 26px; top: 20px; }
  .verified-name {
    font-family: "Source Sans 3", sans-serif;
    font-size: 22px;
    color: #ececec;
    line-height: 1;
  }
  .verified-mark {
    display: flex; align-items: center; gap: 5px;
    margin-left: 85px; margin-top: 4px;
    font-family: "Source Sans 3", sans-serif;
    font-size: 21px;
    color: var(--verified-green);
    line-height: 1;
  }
  .verified-shape { width: 14px; height: 14px; background: var(--verified-green); }
  .brand--back { right: 26px; top: 22px; gap: 6px; }
  .brand--back .brand-square { width: 62px; height: 46px; }
  .brand--back .brand-name { font-size: 23px; line-height: 23px; color: #e4e4e4; }

  .tagline {
    position: absolute; left: 0; right: 0; top: 288px;
    text-align: center;
    font-family: "Source Sans 3", sans-serif;
    font-size: 22px;
    color: var(--ink-light);
  }
  .tagline-rule {
    position: absolute; left: 60px; right: 60px; top: 323px;
    height: 1px;
    background: linear-gradient(90deg, transparent, rgba(255,255,255,0.45), transparent);
  }
  .callback-note {
    position: absolute; left: 0; right: 0; top: 328px;
    text-align: center;
    font-family: "Source Sans 3", sans-serif;
    font-style: italic;
    font-size: 15px;
    color: var(--ink-light);
  }
</style>
</head>
<body>

<section class="card card--front" aria-label="Card front">
  <svg class="front-shape" width="615" height="352" viewBox="0 0 615 352" aria-hidden="true">
    <path d="M0 222 H300 Q318 222 330 218 L330 231 H0 Z" fill="var(--band-grey)"/>
    <path d="M0 234 H318 C338 234 340 203 372 203 H615 V352 H0 Z" fill="var(--brand-red)"/>
  </svg>

  <div class="brand brand--front">
    <span class="brand-square" aria-hidden="true"></span>
    <span class="brand-name">Kites7<br>Market</span>
  </div>

  <div class="portrait" role="img" aria-label="Portrait photo of Tobias Wendler in a circle"></div>

  <h1 class="holder-name">Tobias Wendler</h1>
  <span class="contact-divider" aria-hidden="true"></span>
  <ul class="contact-list">
    <li class="contact-item">
      <svg class="contact-icon" viewBox="0 0 24 24" aria-hidden="true"><path d="M6.6 10.8a15.1 15.1 0 0 0 6.6 6.6l2.2-2.2a1 1 0 0 1 1-.25 11.4 11.4 0 0 0 3.6.57 1 1 0 0 1 1 1V20a1 1 0 0 1-1 1A17 17 0 0 1 3 4a1 1 0 0 1 1-1h3.5a1 1 0 0 1 1 1c0 1.25.2 2.45.57 3.57a1 1 0 0 1-.25 1z"/></svg>
      +49 176 58 20 917
    </li>
    <li class="contact-item">
      <svg class="contact-icon" viewBox="0 0 24 24" aria-hidden="true"><path d="M2 5h20v14H2z M2 5l10 8 10-8" fill="var(--ink-light)" stroke="var(--brand-red)" stroke-width="1.5"/></svg>
      tobias@kites7market.com
    </li>
    <li class="contact-item">
      <svg class="contact-icon" viewBox="0 0 24 24" aria-hidden="true"><circle cx="12" cy="12" r="10"/><path d="M2 12h20M12 2c3 3 3 17 0 20M12 2c-3 3-3 17 0 20" fill="none" stroke="var(--brand-red)" stroke-width="1.5"/></svg>
      www.kites7market.com
    </li>
  </ul>
</section>

<section class="card card--back" aria-label="Card back">
  <div class="venue-photo" role="img" aria-label="360° panorama photo of a cosy restaurant dining room with wooden benches and checked tablecloths"></div>

  <div class="verified-badge">
    <div class="verified-name">Zorvex PanoWalk</div>
    <div class="verified-mark"><span class="verified-shape" aria-hidden="true"></span>verified</div>
  </div>

  <div class="brand brand--back">
    <span class="brand-square" aria-hidden="true"></span>
    <span class="brand-name">Kites7<br>Market</span>
  </div>

  <p class="tagline">360° zorvex pano walk certified photographer</p>
  <span class="tagline-rule" aria-hidden="true"></span>
  <p class="callback-note">send us a sms or chatterly and we call you back.</p>
</section>

</body>
</html>
```